KRT Project Signage

Need a sign to be displayed in the front of properties currently under Construction or Renovation to advertise our company information. Need it to be Professional and Contemporary. We are a Design/Build Construction Company. Information should include Company Name, email, website, phone number. Attached: Logo and company brochure, also included and inspiration images

```html
<!DOCTYPE html>
<html lang="en">
<head>
<meta charset="utf-8">
<title>KRT Project Signage</title>
<link href="https://fonts.googleapis.com/css2?family=League+Spartan:wght@500;600;700&family=Quicksand:wght@600&display=swap" rel="stylesheet">
<style>
  :root {
    --yellow: #f2ea3a;
    --ink: #1e1e1e;
    --panel: rgba(52, 52, 52, 0.92);
    --paper: #ffffff;
    --backdrop: #eeeeec;
  }
  html, body {
    margin: 0;
    padding: 0;
    width: 1200px;
    height: 2864px;
    overflow: hidden;
    background: var(--backdrop);
  }
  .sign {
    position: absolute;
    left: 60px;
    top: 620px;
    width: 886px;
    height: 1331px;
    background: var(--paper);
    transform: scale(1.219);
    transform-origin: top left;
    box-shadow: 0 4px 18px rgba(0,0,0,0.18);
    font-family: "League Spartan", sans-serif;
    color: var(--ink);
  }
  .brand {
    position: absolute;
    left: 0; top: 0;
    width: 100%;
    height: 245px;
    display: flex;
    align-items: center;
    justify-content: center;
    gap: 22px;
  }
  .brand-name {
    font-family: "League Spartan", sans-serif;
    font-weight: 600;
    font-size: 44px;
    letter-spacing: 0.04em;
    color: var(--ink);
    padding-top: 6px;
  }
  .brand-dot {
    width: 34px;
    height: 34px;
    border-radius: 50%;
    background: var(--yellow);
  }
  .project-photo {
    position: absolute;
    left: 0; top: 245px;
    width: 100%;
    height: 650px;
    background:
      linear-gradient(90deg, #e9ecef 0%, #dfe2e5 38%, #cfc8c2 58%, #7a5a45 78%, #5b3e2e 100%);
    border-top: 2px solid #555;
  }
  .name-panel {
    position: absolute;
    left: 160px;
    top: 662px;
    width: 567px;
    height: 334px;
    background: var(--panel);
    display: flex;
    flex-direction: column;
    align-items: center;
    justify-content: center;
    color: var(--yellow);
  }
  .name-line {
    font-weight: 700;
    font-size: 138px;
    line-height: 108px;
    letter-spacing: -0.01em;
    padding-top: 18px;
  }
  .name-role {
    margin-top: 6px;
    font-weight: 600;
    font-size: 40px;
    letter-spacing: 0.2em;
    margin-right: -0.2em;
  }
  .contact {
    position: absolute;
    left: 0;
    width: 100%;
    display: flex;
    align-items: center;
    justify-content: center;
    gap: 22px;
  }
  .contact-phone { top: 1020px; }
  .contact-email { top: 1132px; }
  .contact-web { top: 1212px; }
  .phone-number {
    font-weight: 700;
    font-size: 108px;
    line-height: 1;
    padding-top: 12px;
  }
  .contact-text {
    font-family: "Quicksand", sans-serif;
    font-weight: 600;
    font-size: 52px;
    line-height: 1;
  }
  .icon { display: block; }
</style>
</head>
<body>
  <main class="sign">
    <header class="brand">
      <span class="brand-name">KRT CONSTRUCTION</span>
      <span class="brand-dot"></span>
    </header>

    <div class="project-photo" role="img" aria-label="Photo of a bright modern dining room and kitchen with white walls, framed art, pendant light and dark wood cabinetry"></div>

    <section class="name-panel">
      <div class="name-line">MARCUS</div>
      <div class="name-line">HOLDEN</div>
      <div class="name-role">DESIGN &amp; BUILDER</div>
    </section>

    <div class="contact contact-phone">
      <svg class="icon" width="58" height="58" viewBox="0 0 58 58" aria-hidden="true">
        <circle cx="29" cy="29" r="29" fill="var(--yellow)"/>
        <path d="M20 15c2-1 4 0 5 2l2 5c1 2 0 3-1 4l-2 2c1 3 4 6 7 7l2-2c1-1 2-2 4-1l5 2c2 1 3 3 2 5l-1 3c-1 2-3 3-5 3-11-1-21-11-22-22 0-2 1-4 3-5z" fill="#fff"/>
      </svg>
      <span class="phone-number">555.210.4870</span>
    </div>

    <div class="contact contact-email">
      <svg class="icon" width="34" height="34" viewBox="0 0 34 34" aria-hidden="true">
        <circle cx="17" cy="17" r="17" fill="var(--yellow)"/>
        <rect x="9" y="11" width="16" height="12" rx="2" fill="#fff"/>
        <path d="M9.5 12l7.5 6 7.5-6" fill="none" stroke="var(--yellow)" stroke-width="1.8"/>
      </svg>
      <span class="contact-text">info@krtconstruction.com</span>
    </div>

    <div class="contact contact-web">
      <svg class="icon" width="34" height="34" viewBox="0 0 34 34" aria-hidden="true">
        <circle cx="17" cy="17" r="17" fill="var(--yellow)"/>
        <g fill="none" stroke="#fff" stroke-width="1.6">
          <circle cx="17" cy="17" r="9"/>
          <ellipse cx="17" cy="17" rx="4" ry="9"/>
          <line x1="8" y1="17" x2="26" y2="17"/>
        </g>
      </svg>
      <span class="contact-text">www.krtconstruction.com</span>
    </div>
  </main>
</body>
</html>
```